Website Design - TallyPorchHelpers.net

PLEASE CHECK WORD DOCUMENT ATTACHED FOR WEBSITE FLOW.

Target Market(s)

REAL ESTATE AGENTS ARE THE TARGET MARKET

Industry/Entity Type

Real Estate

Coding

Coded - Design and coding required

Number of Pages Required

4 page

Colors

Designer to choose colors to be used in the design.

Requirements
Must have
• WE LIKE RED LOGO ATTACHED
Nice to have
• PLEASE CHECK WORD DOCUMENT ATTACHED FOR WEBSITE FLOW.
Should not have

```html
<!DOCTYPE html>
<html lang="en">
<head>
<meta charset="utf-8">
<title>Tally Porch Helpers</title>
<link rel="stylesheet" href="https://fonts.googleapis.com/css2?family=Roboto:wght@400;500;700;900&family=Oswald:wght@500&family=Open+Sans:wght@400;600&display=swap">
<style>
:root{
  --red:#e0061b;
  --navy:#27248f;
  --navy-deep:#1d1a78;
  --ink:#222222;
  --grey:#e6e6e6;
  --dark:#1c1c1c;
  --footer-line:#333333;
  --white:#ffffff;
}
*{box-sizing:border-box;margin:0;padding:0}
html,body{width:1200px;height:2922px;overflow:hidden}
body{position:relative;background:var(--white);font-family:"Open Sans",sans-serif;color:var(--ink)}
.abs{position:absolute}

.topbar{left:0;top:0;width:1200px;height:35px;background:var(--red);color:var(--white)}
.topbar .call{left:575px;top:8px;font:700 15px "Roboto",sans-serif;display:flex;align-items:center;gap:10px}
.topbar .search{left:790px;top:7px;width:277px;height:21px;border-radius:11px;background:var(--white);color:#777;font-size:10px;padding:4px 16px}
.topbar .search svg{position:absolute;right:12px;top:5px}

.header{left:0;top:35px;width:1200px;height:88px;background:var(--white)}
.brand{left:132px;top:22px;display:flex;align-items:center;gap:12px;color:var(--navy);font:900 25px/1 "Roboto",sans-serif;letter-spacing:.5px}
.brand .mark{width:40px;height:40px;background:var(--navy)}
.nav{right:88px;top:32px;display:flex;gap:32px;font:500 18px "Roboto",sans-serif;color:var(--ink)}

.hero{left:0;top:123px;width:1200px;height:670px;overflow:hidden}
.hero-photo{left:0;top:0;width:1200px;height:600px;background:linear-gradient(180deg,#8a8f93 0%,#b7b5ad 30%,#8d8a72 55%,#5f7a38 75%,#6b4e35 100%)}
.hero-caption{left:322px;top:253px;width:620px;height:164px;border:3px solid var(--white);background:rgba(30,30,30,.45);color:var(--white);font:500 25px/41px "Oswald",sans-serif;text-align:center;text-transform:uppercase;padding:14px 26px;border-radius:6px}
.hero-band{left:0;top:540px}
.dots{left:570px;top:752px;display:flex;gap:6px}
.dots span{width:14px;height:14px;border-radius:50%;border:2px solid var(--navy);background:var(--white)}
.dots span.on{background:var(--navy);border-color:var(--white);box-shadow:0 0 0 1px var(--navy)}

.choose{left:0;top:800px;width:1200px;height:317px;background:linear-gradient(180deg,#fff 0%,#f4f4f7 100%)}
.choose h2{position:absolute;left:0;top:60px;width:1200px;text-align:center;font:500 30px/40px "Roboto",sans-serif;color:var(--ink)}
.options{position:absolute;left:178px;top:173px;display:flex;gap:18px}
.options span{height:38px;padding:0 24px;border:2px solid var(--navy);border-radius:20px;font:500 16px/34px "Roboto",sans-serif;color:var(--navy);background:var(--white)}
.options span.active{background:var(--red);border-color:var(--red);color:var(--white)}

.pricing{left:0;top:1117px;width:1200px;height:583px;background:var(--navy)}
.pricing h2{position:absolute;left:0;top:62px;width:1200px;text-align:center;font:700 38px "Roboto",sans-serif;color:var(--white)}
.plan{top:185px;width:230px;height:385px;background:var(--white)}
.plan .head{height:130px;background:var(--grey);position:relative}
.plan .badge{position:absolute;left:70px;top:20px;width:90px;height:90px;border-radius:50%;background:var(--navy);color:var(--white);text-align:center;font:700 27px/1 "Roboto",sans-serif;padding-top:18px}
.plan .badge small{display:block;font-size:17px;margin-top:2px}
.plan ul{list-style:none;padding:18px 14px 0 14px}
.plan li{position:relative;padding-left:28px;font-size:11.5px;line-height:20px;margin-bottom:10px}
.plan li svg{position:absolute;left:0;top:5px}
.plan .buy{position:absolute;left:13px;top:327px;width:110px;height:32px;background:var(--navy);color:var(--white);font:700 13px/32px "Roboto",sans-serif;text-align:center;border-radius:3px}

.perks h2{position:absolute;left:0;top:1785px;width:1200px;text-align:center;font:500 31px/50px "Roboto",sans-serif;letter-spacing:.5px;color:var(--ink)}
.perk{top:1940px;width:230px;text-align:center}
.perk .ring{margin:0 auto;width:112px;height:112px;border-radius:50%;border:4px solid var(--red);display:flex;align-items:center;justify-content:center}
.perk .ring i{width:86px;height:86px;border-radius:50%;background:var(--red);display:flex;align-items:center;justify-content:center}
.perk h3{margin-top:18px;font:700 23px "Roboto",sans-serif;color:var(--navy)}
.perk p{margin-top:10px;font-size:13px;line-height:22px;padding:0 18px}

.footer{left:0;top:2383px;width:1200px;height:539px;background:var(--dark);color:var(--white)}
.signup{left:132px;top:2310px;width:936px;height:152px;background:linear-gradient(90deg,#3b3799 0%,#4a46a8 50%,#35318f 100%)}
.signup .field{position:absolute;left:188px;top:52px;width:446px;height:40px;border-radius:20px 0 0 20px;background:var(--white);color:#777;font-size:12px;padding:12px 22px}
.signup .go{position:absolute;left:630px;top:52px;width:120px;height:40px;border-radius:0 20px 20px 0;background:var(--red);font:700 14px/40px "Roboto",sans-serif;text-align:center;color:var(--white)}
.fcol{color:var(--white)}
.fcol h4{font:500 21px/30px "Roboto",sans-serif;text-transform:uppercase}
.about{left:132px;top:2522px;width:320px}
.about p{margin-top:20px;font-size:12.5px;line-height:22px;color:#e0e0e0}
.contact{left:488px;top:2522px;width:240px}
.contact .row{position:relative;padding-left:32px;font-size:12px;line-height:19px;margin-top:18px}
.contact .row:first-of-type{margin-top:22px}
.contact .row svg{position:absolute;left:0;top:2px}
.links{left:738px;top:2522px}
.links ul{list-style:none;margin-top:22px}
.links li{font-size:11.5px;line-height:22px;padding-left:20px;position:relative}
.links li:before{content:"";position:absolute;left:4px;top:8px;border-left:5px solid var(--white);border-top:3px solid transparent;border-bottom:3px solid transparent}
.fbrand{left:902px;top:2536px;display:flex;align-items:center;gap:10px;font:900 23px/1 "Roboto",sans-serif;color:var(--white)}
.fbrand .mark{width:34px;height:34px;background:var(--white)}
.socials{left:928px;top:2628px;display:flex;gap:7px}
.socials span{width:30px;height:30px;border-radius:50%;border:2px solid var(--white)}
.bottom{left:0;top:2800px;width:1200px;border-top:1px solid var(--footer-line);text-align:center;font-size:12px;line-height:30px;padding-top:30px;color:var(--white)}
</style>
</head>
<body>

<div class="abs topbar">
  <div class="abs call">
    <svg width="12" height="12" viewBox="0 0 24 24"><path fill="#fff" d="M6.6 10.8a15 15 0 006.6 6.6l2.2-2.2a1 1 0 011-.25 11 11 0 003.6.6 1 1 0 011 1V20a1 1 0 01-1 1A17 17 0 013 4a1 1 0 011-1h3.5a1 1 0 011 1 11 11 0 00.6 3.6 1 1 0 01-.25 1z"/></svg>
    Call Us : 1800 555 0147
  </div>
  <div class="abs search">Search item
    <svg width="10" height="10" viewBox="0 0 20 20"><circle cx="8" cy="8" r="6" fill="none" stroke="#222" stroke-width="2.5"/><path d="M12.5 12.5L18 18" stroke="#222" stroke-width="2.5"/></svg>
  </div>
</div>

<header class="abs header">
  <div class="abs brand"><span class="mark"></span><span>TALLY PORCH<br>HELPERS</span></div>
  <nav class="abs nav"><span>How It Works</span><span>Service Area</span><span>Pricing</span><span>About Us</span><span>Faq</span></nav>
</header>

<section class="abs hero">
  <div class="abs hero-photo" role="img" aria-label="Photo of a two-storey suburban house with landscaped garden and an open house sign on a post"></div>
  <p class="abs hero-caption">Helping agents save time and money. We place signs and boost foot traffic to your open houses using proven marketing techniques.</p>
  <svg class="abs hero-band" width="1200" height="130" viewBox="0 0 1200 130"><path d="M0 0 L600 40 L1200 0 L1200 48 L600 128 L0 48 Z" fill="#27248f"/><path d="M0 48 L600 128 L1200 48 L1200 130 L0 130 Z" fill="#fff"/></svg>
</section>
<div class="abs dots"><span class="on"></span><span></span><span></span></div>

<section class="abs choose">
  <h2>CHOOSE THE OPTION BELOW THAT<br>BEST DESCRIBES YOU</h2>
  <div class="options"><span>I'M A FULL ON BROKERAGE</span><span class="active">I'M&nbsp; AN IND. BROKER WITH A TEAM</span><span>I NEED SIGN PLACEMENT ASAP</span></div>
</section>

<section class="abs pricing">
  <h2>PRICING</h2>
</section>

<div class="abs plan" style="left:0;top:1302px">
  <div class="head"><div class="badge">5<small>SIGNS</small></div></div>
  <ul>
    <li><svg width="11" height="9" viewBox="0 0 11 9"><path d="M1 4.5L4 7.5L10 1" fill="none" stroke="#e0061b" stroke-width="2"/></svg>Place signs strategically in best areas according to where the open house is located</li>
    <li><svg width="11" height="9" viewBox="0 0 11 9"><path d="M1 4.5L4 7.5L10 1" fill="none" stroke="#e0061b" stroke-width="2"/></svg>Pick Up the signs after the open house</li>
    <li><svg width="11" height="9" viewBox="0 0 11 9"><path d="M1 4.5L4 7.5L10 1" fill="none" stroke="#e0061b" stroke-width="2"/></svg>Store custom signs for you if needed</li>
  </ul>
  <div class="buy">BUY NOW</div>
</div>
<div class="abs plan" style="left:243px;top:1302px">
  <div class="head"><div class="badge">10<small>SIGNS</small></div></div>
  <ul>
    <li><svg width="11" height="9" viewBox="0 0 11 9"><path d="M1 4.5L4 7.5L10 1" fill="none" stroke="#e0061b" stroke-width="2"/></svg>Place signs strategically in best areas according to where the open house is located</li>
    <li><svg width="11" height="9" viewBox="0 0 11 9"><path d="M1 4.5L4 7.5L10 1" fill="none" stroke="#e0061b" stroke-width="2"/></svg>Pick Up the signs after the open house</li>
    <li><svg width="11" height="9" viewBox="0 0 11 9"><path d="M1 4.5L4 7.5L10 1" fill="none" stroke="#e0061b" stroke-width="2"/></svg>Store custom signs for you if needed</li>
  </ul>
  <div class="buy">BUY NOW</div>
</div>
<div class="abs plan" style="left:485px;top:1302px">
  <div class="head"><div class="badge">15<small>SIGNS</small></div></div>
  <ul>
    <li><svg width="11" height="9" viewBox="0 0 11 9"><path d="M1 4.5L4 7.5L10 1" fill="none" stroke="#e0061b" stroke-width="2"/></svg>Place signs strategically in best areas according to where the open house is located</li>
    <li><svg width="11" height="9" viewBox="0 0 11 9"><path d="M1 4.5L4 7.5L10 1" fill="none" stroke="#e0061b" stroke-width="2"/></svg>Pick Up the signs after the open house</li>
    <li><svg width="11" height="9" viewBox="0 0 11 9"><path d="M1 4.5L4 7.5L10 1" fill="none" stroke="#e0061b" stroke-width="2"/></svg>Store custom signs for you if needed</li>
  </ul>
  <div class="buy">BUY NOW</div>
</div>
<div class="abs plan" style="left:727px;top:1302px">
  <div class="head"><div class="badge">20<small>SIGNS</small></div></div>
  <ul>
    <li><svg width="11" height="9" viewBox="0 0 11 9"><path d="M1 4.5L4 7.5L10 1" fill="none" stroke="#e0061b" stroke-width="2"/></svg>Place signs strategically in best areas according to where the open house is located</li>
    <li><svg width="11" height="9" viewBox="0 0 11 9"><path d="M1 4.5L4 7.5L10 1" fill="none" stroke="#e0061b" stroke-width="2"/></svg>Pick Up the signs after the open house</li>
    <li><svg width="11" height="9" viewBox="0 0 11 9"><path d="M1 4.5L4 7.5L10 1" fill="none" stroke="#e0061b" stroke-width="2"/></svg>Store custom signs for you if needed</li>
  </ul>
  <div class="buy">BUY NOW</div>
</div>
<div class="abs plan" style="left:969px;top:1302px;width:231px">
  <div class="head"><div class="badge">25<small>SIGNS</small></div></div>
  <ul>
    <li><svg width="11" height="9" viewBox="0 0 11 9"><path d="M1 4.5L4 7.5L10 1" fill="none" stroke="#e0061b" stroke-width="2"/></svg>Place signs strategically in best areas according to where the open house is located</li>
    <li><svg width="11" height="9" viewBox="0 0 11 9"><path d="M1 4.5L4 7.5L10 1" fill="none" stroke="#e0061b" stroke-width="2"/></svg>Pick Up the signs after the open house</li>
    <li><svg width="11" height="9" viewBox="0 0 11 9"><path d="M1 4.5L4 7.5L10 1" fill="none" stroke="#e0061b" stroke-width="2"/></svg>Store custom signs for you if needed</li>
  </ul>
  <div class="buy">BUY NOW</div>
</div>

<section class="perks">
  <h2>SIGN UP FOR A SUBSCRIPTION AND GET THESE<br>MARKETING SERVICES FOR FREE</h2>
  <div class="abs perk" style="left:115px">
    <div class="ring"><i><svg width="44" height="38" viewBox="0 0 44 38"><ellipse cx="17" cy="14" rx="16" ry="12" fill="#fff"/><path d="M8 22 L4 32 L16 25Z" fill="#fff"/><ellipse cx="30" cy="21" rx="13" ry="10" fill="#fff" stroke="#e0061b" stroke-width="2"/></svg></i></div>
    <h3>SMS</h3>
    <p>Send sms blast to your neighborhood informing them your home is for sale and if they know anyone looking to send them over</p>
  </div>
  <div class="abs perk" style="left:363px">
    <div class="ring"><i><svg width="44" height="32" viewBox="0 0 44 32"><rect x="1" y="1" width="42" height="30" rx="3" fill="#fff"/><path d="M2 3 L22 18 L42 3" fill="none" stroke="#e0061b" stroke-width="3"/></svg></i></div>
    <h3>EMAIL</h3>
    <p>email blast to your neighborhood informing them your home is for sale and if they know anyone looking to send them over</p>
  </div>
  <div class="abs perk" style="left:611px">
    <div class="ring"><i><svg width="38" height="38" viewBox="0 0 38 38"><rect x="1" y="1" width="36" height="36" rx="5" fill="#fff"/></svg></i></div>
    <h3>SOCIAL AD</h3>
    <p>Newsfeed ads to people in your open house area</p>
  </div>
  <div class="abs perk" style="left:859px">
    <div class="ring"><i><svg width="42" height="42" viewBox="0 0 42 42"><path d="M3 4 L18 3 L39 24 L24 39 L3 18Z" fill="#fff"/><circle cx="11" cy="11" r="3" fill="#e0061b"/></svg></i></div>
    <h3>VB</h3>
    <p>VB blast to your neighborhood informing them your home is for sale and if they know anyone looking to send them over</p>
  </div>
</section>

<footer class="abs footer"></footer>
<div class="abs signup" role="img" aria-label="Dim blue-tinted photo of a house front behind the newsletter form">
  <div class="field">Enter your E - mail</div>
  <div class="go">SUBSCRIBE</div>
</div>

<div class="abs fcol about">
  <h4>About Tally Porch<br>Helpers</h4>
  <p>Sed ut perspiciatis unde omnis iste natus error sit voluptatem accusantium doloremque laudantium, totam rem aperiam, eaque ipsa quae ab illo inventore veritatis et quasi architecto beatae vitae dicta sunt explicabo. Nemo enim ipsam</p>
</div>
<div class="abs fcol contact">
  <h4>Contact Us</h4>
  <div class="row"><svg width="14" height="16" viewBox="0 0 14 18"><path d="M7 0a7 7 0 00-7 7c0 5 7 11 7 11s7-6 7-11a7 7 0 00-7-7z" fill="#fff"/><circle cx="7" cy="7" r="2.5" fill="#1c1c1c"/></svg>Tally Porch Helpers<br>42, 7781 LB. Dunmere</div>
  <div class="row"><svg width="14" height="14" viewBox="0 0 24 24"><path fill="#fff" d="M6.6 10.8a15 15 0 006.6 6.6l2.2-2.2a1 1 0 011-.25 11 11 0 003.6.6 1 1 0 011 1V20a1 1 0 01-1 1A17 17 0 013 4a1 1 0 011-1h3.5a1 1 0 011 1 11 11 0 00.6 3.6 1 1 0 01-.25 1z"/></svg>Phone: 020 5550 1934</div>
  <div class="row"><svg width="14" height="11" viewBox="0 0 14 11"><rect width="14" height="11" rx="1" fill="#fff"/><path d="M1 1L7 6L13 1" fill="none" stroke="#1c1c1c" stroke-width="1.3"/></svg>info@tallyporchhelpers.net</div>
  <div class="row"><svg width="14" height="14" viewBox="0 0 14 14"><circle cx="7" cy="7" r="6" fill="none" stroke="#fff" stroke-width="1.6"/><path d="M7 3.5V7H10" fill="none" stroke="#fff" stroke-width="1.6"/></svg>Man - Sun: 8:00 - 22:00</div>
</div>
<div class="abs fcol links">
  <h4>Quick Links</h4>
  <ul><li>How It Works</li><li>Service Area</li><li>Pricing</li><li>About Us</li><li>Faq</li></ul>
</div>
<div class="abs fbrand"><span class="mark"></span><span>TALLY PORCH<br>HELPERS</span></div>
<div class="abs socials"><span></span><span></span><span></span><span></span></div>
<div class="abs bottom">© Copyright 2018 Tally Porch Helpers. All Rights Reserved.<br>Terms and Conditions | Privacy Policy</div>

</body>
</html>
```